Fast Growing Personal Injury Law Firm Needs Business Card Design

We need a business card design for a fast growing personal injury law firm in Florida. Our name is Dorian Kalvenfeld, P.A. Our practice is comprised of younger attorneys (in their 30s) that employ more modern techniques/tools than our older competition. We would prefer a look that is a modern play on a classic look. Also, we would like to continue using a color scheme that employs navy blue and kelly green (other shades of green could be fine too) as well as our "E" logo.

Industry/Entity Type

Law Firm

```html
<!DOCTYPE html>
<html lang="en">
<head>
<meta charset="utf-8">
<title>Dorian Kalvenfeld, P.A. — Stationery Set</title>
<link rel="stylesheet" href="https://fonts.googleapis.com/css2?family=Source+Sans+3:wght@400;600&display=swap">
<style>
  :root {
    --backdrop: #5e5e5e;
    --paper: #ffffff;
    --paper-tint: #f3f4f7;
    --green: #0e8747;
    --navy: #1f325d;
    --ink: #3a3f4a;
    --accent-red: #d2232a;
    --dieline: #e79aa4;
    --fold: #b9bcc4;
  }
  * { box-sizing: border-box; margin: 0; padding: 0; }
  html, body { width: 1200px; height: 839px; overflow: hidden; }
  body {
    position: relative;
    background: var(--backdrop);
    font-family: "Source Sans 3", "Myriad Pro", sans-serif;
    color: var(--ink);
  }
  .abs { position: absolute; }
  .sheet { position: absolute; background: var(--paper); }
  .tint { position: absolute; background: var(--paper-tint); }
  .green { background: var(--green); }
  .navy { background: var(--navy); }

  /* brand stand-in: plain square + wordmark */
  .brand {
    position: absolute; display: flex; align-items: center; justify-content: center;
    gap: 3px; font-weight: 600; color: var(--navy); white-space: nowrap; line-height: 1;
  }
  .brand i { display: block; background: var(--green); flex: none; }
  .brand.on-dark { color: #fff; }
  .brand.on-dark i { background: #fff; }

  .contact { position: absolute; font-size: 4.2px; line-height: 6px; color: var(--ink); white-space: nowrap; }
  .contact .rule { display: inline-block; width: 22px; height: 2px; vertical-align: middle; margin-right: 4px; }
  .contact.right { text-align: right; }
  .contact.right .rule { margin: 0 0 0 4px; width: 26px; }

  .web { position: absolute; font-size: 7px; color: var(--navy); }
  .bar { position: absolute; display: flex; }
  .bar span { height: 100%; }

  .outline { position: absolute; left: 0; top: 0; pointer-events: none; }
</style>
</head>
<body>

<!-- Letterhead -->
<section class="letterhead">
  <div class="sheet" style="left:57px;top:31px;width:342px;height:434px"></div>
  <div class="tint" style="left:65px;top:38px;width:330px;height:420px"></div>
  <div class="brand" style="left:80px;top:68px;font-size:6px"><i style="width:8px;height:8px"></i>Kalvenfeld</div>
  <div class="contact right" style="left:232px;top:74px;width:160px">
    2150 Harbor View Drive Suite 410 Palmetto Grove, Florida 34288<span class="rule green"></span><br>
    T (941) 555-0142 F (941) 555-0178 E dorian@kalvenfeldlaw.com<span class="rule navy"></span>
  </div>
  <div class="bar" style="left:65px;top:450px;width:327px;height:8px">
    <span class="green" style="width:263px"></span><span class="navy" style="width:19px"></span><span class="green" style="width:20px"></span><span class="navy" style="width:25px"></span>
  </div>
</section>

<!-- Presentation folder -->
<section class="folder">
  <div class="sheet" style="left:437px;top:35px;width:744px;height:628px"></div>
  <div class="abs green" style="left:468px;top:45px;width:340px;height:406px"></div>
  <div class="abs navy" style="left:808px;top:45px;width:341px;height:406px"></div>
  <div class="brand on-dark" style="left:598px;top:232px;width:84px;font-size:14px"><i style="width:14px;height:14px"></i>Kalvenfeld</div>
  <div class="brand on-dark" style="left:1030px;top:92px;width:84px;font-size:13px"><i style="width:13px;height:13px"></i>Kalvenfeld</div>
  <div class="contact" style="left:468px;top:460px">
    <span class="rule green"></span>2150 Harbor View Drive Suite 410 Palmetto Grove, Florida 34288<br>
    <span class="rule navy"></span>T (941) 555-0142 F (941) 555-0178 E dorian@kalvenfeldlaw.com
  </div>
  <div class="web" style="left:821px;top:461px">www.kalvenfeldlaw.com</div>
  <div class="bar" style="left:468px;top:479px;width:681px;height:17px">
    <span class="green" style="width:613px"></span><span class="navy" style="width:21px"></span><span class="green" style="width:21px"></span><span class="navy" style="width:26px"></span>
  </div>
</section>

<!-- Envelope -->
<section class="envelope">
  <div class="sheet" style="left:9px;top:480px;width:412px;height:354px"></div>
  <svg class="abs" style="left:33px;top:490px" width="364" height="69" viewBox="0 0 364 69" aria-hidden="true">
    <path d="M0 69 L14 8 Q16 0 26 0 L338 0 Q348 0 350 8 L364 69 Z" fill="var(--green)"/>
  </svg>
  <div class="brand on-dark" style="left:183px;top:518px;width:60px;font-size:6px"><i style="width:6px;height:6px"></i>Kalvenfeld</div>
  <div class="tint" style="left:40px;top:559px;width:352px;height:166px"></div>
  <div class="brand" style="left:296px;top:588px;width:88px;font-size:12px"><i style="width:12px;height:12px"></i>Kalvenfeld</div>
  <div class="abs" style="left:66px;top:631px;width:150px;height:46px;border:1px solid var(--dieline);border-radius:8px"></div>
  <div class="contact" style="left:38px;top:690px">
    <span class="rule green"></span>2150 Harbor View Drive Suite 410 Palmetto Grove, Florida 34288<br>
    <span class="rule navy"></span>T (941) 555-0142 F (941) 555-0178 E dorian@kalvenfeldlaw.com
  </div>
  <div class="bar" style="left:42px;top:725px;width:349px;height:18px">
    <span class="green" style="width:280px;display:flex;align-items:center;justify-content:center;color:#fff;font-size:7px">www.kalvenfeldlaw.com</span><span class="navy" style="width:22px"></span><span class="green" style="width:20px"></span><span class="navy" style="width:27px"></span>
  </div>
</section>

<!-- Compliments slip -->
<section class="compliments-slip">
  <div class="sheet" style="left:433px;top:675px;width:342px;height:159px"></div>
  <div class="tint" style="left:440px;top:682px;width:328px;height:144px"></div>
  <div class="abs" style="left:481px;top:710px;font-size:12.5px;color:#222">WithCompliments</div>
  <div class="brand" style="left:690px;top:710px;width:66px;font-size:9px"><i style="width:9px;height:9px"></i>Kalvenfeld</div>
  <div class="contact" style="left:440px;top:803px">
    <span class="rule green"></span>2150 Harbor View Drive Suite 410 Palmetto Grove, Florida 34288<br>
    <span class="rule navy"></span>T (941) 555-0142 F (941) 555-0178 E dorian@kalvenfeldlaw.com
  </div>
  <div class="bar" style="left:440px;top:818px;width:328px;height:8px">
    <span class="green" style="width:264px"></span><span class="navy" style="width:19px"></span><span class="green" style="width:20px"></span><span class="navy" style="width:25px"></span>
  </div>
</section>

<!-- Business card front -->
<section class="business-card front">
  <div class="sheet" style="left:786px;top:707px;width:156px;height:99px"></div>
  <div class="abs green" style="left:795px;top:716px;width:138px;height:63px"></div>
  <div class="brand on-dark" style="left:830px;top:740px;width:68px;font-size:9px"><i style="width:9px;height:9px"></i>Kalvenfeld</div>
  <div class="abs" style="left:795px;top:765px;width:138px;text-align:center;font-size:7.5px;color:#fff">Personal Injury Attorneys</div>
  <div class="abs" style="left:795px;top:781px;width:138px;text-align:center;font-size:4.5px;color:var(--navy)">www.kalvenfeldlaw.com</div>
  <div class="abs green" style="left:795px;top:789px;width:138px;height:11px"></div>
</section>

<!-- Business card back -->
<section class="business-card back">
  <div class="sheet" style="left:964px;top:709px;width:155px;height:97px"></div>
  <div class="tint" style="left:972px;top:716px;width:140px;height:84px"></div>
  <div class="abs" style="left:975px;top:728px;width:68px;height:24px;background:#e4e5ea"></div>
  <div class="abs" style="left:979px;top:732px;font-size:5.5px;color:var(--navy);white-space:nowrap">Dorian Kalvenfeld, P.A.</div>
  <div class="abs" style="left:979px;top:740px;font-size:4px;color:var(--accent-red)">Attorney at Law</div>
  <div class="brand" style="left:1052px;top:736px;width:46px;font-size:6px"><i style="width:6px;height:6px"></i>Kalvenfeld</div>
  <div class="contact" style="left:972px;top:778px;font-size:3.4px;line-height:5.5px">
    <span class="rule green"></span>2150 Harbor View Drive Suite 410 Palmetto Grove, FL 34288<br>
    <span class="rule navy"></span>T (941) 555-0142 F (941) 555-0178 E dorian@kalvenfeldlaw.com
  </div>
</section>

<!-- Die lines and folds -->
<svg class="outline" width="1200" height="839" viewBox="0 0 1200 839" aria-hidden="true">
  <g fill="none" stroke="var(--dieline)" stroke-width="0.8">
    <path d="M468 497 L455 510 L455 635 L475 648 L795 648 L808 497"/>
    <path d="M808 497 L820 648 L1145 648 L1165 635 L1165 510 L1149 497"/>
    <path d="M40 560 L22 568 L22 712 L40 720"/>
    <path d="M392 560 L410 568 L410 712 L392 720"/>
    <path d="M42 743 L42 814 Q42 828 58 828 L375 828 Q391 828 391 814 L391 743"/>
    <line x1="468" y1="52" x2="1149" y2="52"/>
  </g>
  <g fill="none" stroke="var(--fold)" stroke-width="0.7" stroke-dasharray="3 2">
    <rect x="474" y="497" width="669" height="151"/>
    <line x1="808" y1="45" x2="808" y2="497"/>
  </g>
  <g stroke="var(--fold)" stroke-width="0.9">
    <line x1="929" y1="549" x2="942" y2="536"/>
    <line x1="1050" y1="536" x2="1063" y2="549"/>
    <line x1="929" y1="599" x2="942" y2="612"/>
    <line x1="1050" y1="612" x2="1063" y2="599"/>
  </g>
</svg>

</body>
</html>
```